Bramwell Lodge Business Cards design with a logo

I want two Business cards designed with a very modern contemporary logo UNING 1920'S FONT STYLES with the following details

Address:
Bramwell Lodge
17 Pellham Road
Ardencairn
G83 2RN

Details for card 1

Name: Dermot Ashby
email: Dermot.ashby@bramwell.lodge
Tel : +971 52 318 6094
Tel +44 7700 900 318

Details Card 2

Name: Dermot Ashby
email: Neville.osgood@bramwell.lodge
Tel : +971 52 430 9187

Bramwell lodge is a house that was built around 1880 and was used extensively in the 1920's for entertaining and parties in the arts scene, the house again will be resurrected to a modern entertainment venue

If you have any questions feel free to ask

Target Market(s)

The market for this is the young modern crowd

Industry/Entity Type

Entertainment Industry

Contact Information for Business Card

Address:
Bramwell Lodge
17 Pellham Road
Ardencairn
G83 2RN

Details for card 1

Name: Dermot Ashby
Tel : +971 52 318 6094
Tel +44 7700 900 318

Details Card 2

Name: Neville Osgood
Tel : +971 52 430 9187

Logo Text

Bramwell Lodge

Font styles to use
Other font styles liked:
• 1920'S FONT STULES

Requirements
Must have
• Modern Contemporary, whilst taking into consideration the age of the house as detailed above. YOU MUT BE USING 1920'S FONT STYLES
Nice to have
• 1920'S FONT STYLES see attached image if a suggestion
Should not have
• Should not look old or dated

```html
<!DOCTYPE html>
<html lang="en">
<head>
<meta charset="utf-8">
<title>Bramwell Lodge Business Cards</title>
<link href="https://fonts.googleapis.com/css2?family=Federo&family=Poiret+One&display=swap" rel="stylesheet">
<style>
  :root {
    --backdrop: #1c1c1d;
    --card: #161617;
    --card-edge: #242425;
    --pattern-dark: #121213;
    --pattern-light: #2a2a2c;
    --silver: #d9d9db;
    --silver-dim: #9a9a9d;
    --ink-gloss: #0c0c0d;
    --ink-gloss-edge: #3a3a3c;
  }
  * { box-sizing: border-box; margin: 0; padding: 0; }
  html, body {
    width: 1200px; height: 900px; overflow: hidden;
    background: var(--backdrop);
  }
  .canvas {
    position: relative; width: 1200px; height: 900px;
    display: flex; flex-direction: column; align-items: center; justify-content: center; gap: 40px;
  }
  .card {
    position: relative; width: 620px; height: 354px;
    background: var(--card);
    border: 1px solid var(--card-edge);
    box-shadow: 0 18px 40px rgba(0,0,0,.55);
    overflow: hidden;
  }

  /* Front */
  .card-front .pattern-field {
    position: absolute; inset: 0;
    background: linear-gradient(135deg, var(--pattern-dark) 0%, var(--pattern-light) 55%, var(--pattern-dark) 100%);
  }
  .brand {
    position: absolute; left: 0; right: 0; top: 128px;
    display: flex; flex-direction: column; align-items: center; gap: 26px;
  }
  .brand-name {
    display: flex; align-items: center; gap: 16px;
    font-family: "Federo", sans-serif;
    font-size: 44px; letter-spacing: 3px; text-transform: uppercase;
    color: var(--silver);
  }
  .brand-mark { width: 14px; height: 14px; background: var(--silver); }
  .brand-web {
    font-family: "Poiret One", sans-serif;
    font-size: 15px; letter-spacing: 1.5px; text-transform: uppercase;
    color: var(--silver-dim);
  }

  /* Back */
  .card-back .holder {
    position: absolute; left: 48px; top: 140px;
    display: flex; align-items: center; gap: 22px;
  }
  .holder-name {
    font-family: "Federo", sans-serif; font-weight: 400;
    font-size: 27px; letter-spacing: 2px; text-transform: uppercase;
    color: var(--ink-gloss);
    text-shadow: 0 1px 0 var(--ink-gloss-edge), 0 -1px 0 #050505;
  }
  .divider { width: 1px; height: 42px; background: #3b3b3d; }
  .contact-list {
    list-style: none; display: flex; flex-direction: column; gap: 6px;
    font-family: "Poiret One", sans-serif;
    font-size: 14px; letter-spacing: .8px; text-transform: uppercase;
    color: var(--silver);
  }
  .contact-list li { display: flex; align-items: center; gap: 10px; }
  .contact-list svg { width: 11px; height: 11px; flex: none; }
  .address {
    position: absolute; left: 48px; bottom: 44px;
    display: flex; align-items: center; gap: 16px;
    font-family: "Federo", sans-serif;
    font-size: 14px; letter-spacing: 1.6px; text-transform: uppercase;
    color: var(--ink-gloss);
    text-shadow: 0 1px 0 var(--ink-gloss-edge);
    white-space: nowrap;
  }
  .address-mark {
    width: 16px; height: 16px; background: var(--ink-gloss);
    box-shadow: 0 1px 0 var(--ink-gloss-edge);
  }
  .address-text .city { color: var(--silver); text-shadow: none; }
</style>
</head>
<body>
<main class="canvas">
  <section class="card card-front">
    <div class="pattern-field" role="img" aria-label="Embossed art deco pattern of nested diamonds across the card"></div>
    <div class="brand">
      <div class="brand-name"><span class="brand-mark"></span><span>Bramwell Lodge</span></div>
      <div class="brand-web">www.bramwell.lodge</div>
    </div>
  </section>

  <section class="card card-back">
    <div class="holder">
      <h1 class="holder-name">Dermot Ashby</h1>
      <span class="divider"></span>
      <ul class="contact-list">
        <li>
          <svg viewBox="0 0 12 12" aria-hidden="true"><path d="M2.5 1h2l1 2.5-1.3 1a6 6 0 0 0 3.3 3.3l1-1.3L11 7.5v2A1.5 1.5 0 0 1 9.5 11 8.5 8.5 0 0 1 1 2.5 1.5 1.5 0 0 1 2.5 1z" fill="none" stroke="currentColor" stroke-width="1"/></svg>
          <span>+971 52 430 9187</span>
        </li>
        <li>
          <svg viewBox="0 0 12 12" aria-hidden="true"><rect x="1" y="2.5" width="10" height="7" fill="none" stroke="currentColor" stroke-width="1"/><path d="M1 2.5l5 4 5-4" fill="none" stroke="currentColor" stroke-width="1"/></svg>
          <span>Neville.osgood@bramwell.lodge</span>
        </li>
      </ul>
    </div>
    <div class="address">
      <span class="address-mark"></span>
      <span class="address-text">Bramwell Lodge, 17 Pellham Road, <span class="city">Ardencairn, G83 2RN</span></span>
    </div>
  </section>
</main>
</body>
</html>
```